Kelvaro.ch is looking for business card letterhead and envelope C5 with WOW effect

We need a strong business card for our company Kelvaro.ch, logo is available. You want a black or dark background on which the logo Stark r% 26 # 252; appears. Letterhead and envelope in C5 format should be in a similar design, but does not have to be We need a strong business card for our company Kelvaro.ch, logo is available. A black or dark background is desired, on which the logo Stark comes across. The letterhead and the envelope in C5 format should have a similar design.

Target Market(s)

Private customers as well as entrepreneurs

Contact Information for Business Card

E-mail: info@kelvaro-example.ch
Web.www.Kelvaro-example.ch
Tel: +41 ( 0 ) 79 482 6037
Adresse:
Lindenweg 14
9406 Tarnbach

Hier kann man Icons verwenden für Email,Tel und Adressse

Font styles to use
Other font styles liked:
• Dubai,bold

Colors

Designer to choose colors to be used in the design.

Requirements
Must have
• WOW effect
Nice to have
• R% 26 # 252; back business card with our service listings. - VEHICLE LABELING - SHOP WINDOW LABELING - STICKERS AND MUCH MORE ... in red color

```html
<!DOCTYPE html>
<html lang="en">
<head>
<meta charset="utf-8">
<title>Kelvaro.ch business card</title>
<link rel="stylesheet" href="https://fonts.googleapis.com/css2?family=Exo+2:wght@500;600;800&display=swap">
<style>
  :root {
    --backdrop: #8a5a32;
    --card-light: #2b241e;
    --card-dark: #141110;
    --ink: #e6cfae;
    --accent: #d42a2a;
    --rule: #8a6f52;
  }
  * { margin: 0; padding: 0; box-sizing: border-box; }
  html, body { width: 1200px; height: 900px; overflow: hidden; }
  body {
    background: var(--backdrop);
    font-family: "Exo 2", sans-serif;
    color: var(--ink);
  }
  .canvas { position: relative; width: 1200px; height: 900px; }
  .card {
    position: absolute;
    left: 330px;
    width: 557px;
    height: 344px;
    background: linear-gradient(160deg, var(--card-light) 0%, var(--card-dark) 100%);
    text-align: center;
  }
  .card--front { top: 90px; }
  .card--back { top: 468px; }

  .wordmark {
    font-weight: 800;
    text-transform: uppercase;
    letter-spacing: 1px;
    line-height: 1;
  }
  .card--front .wordmark {
    position: absolute;
    top: 104px; left: 0; right: 0;
    font-size: 51px;
  }
  .contact {
    position: absolute;
    top: 220px; left: 0; right: 0;
    font-size: 18px;
    font-weight: 500;
    line-height: 26px;
  }
  .contact__rule {
    width: 180px;
    height: 1px;
    margin: 6px auto 4px;
    background: var(--rule);
  }
  .contact__address { font-size: 19px; }

  .brand-lockup {
    position: absolute;
    top: 118px; left: 122px;
    display: flex;
    align-items: center;
    gap: 24px;
  }
  .brand-lockup__mark {
    width: 80px; height: 80px;
    background: var(--ink);
  }
  .card--back .wordmark { font-size: 35px; }
  .services {
    position: absolute;
    top: 270px; left: 0; right: 0;
    font-size: 16.5px;
    font-weight: 600;
    text-transform: uppercase;
    line-height: 22px;
    color: var(--accent);
  }
</style>
</head>
<body>
<main class="canvas">
  <section class="card card--front">
    <h1 class="wordmark">Kelvaro.ch</h1>
    <div class="contact">
      <p class="contact__line">P: +41 ( 0 ) 79 482 6037 | E: info@kelvaro-example.ch</p>
      <p class="contact__line">W: www.Kelvaro-example.ch</p>
      <div class="contact__rule"></div>
      <p class="contact__address">Lindenweg 14,9406 Tarnbach</p>
    </div>
  </section>

  <section class="card card--back">
    <div class="brand-lockup">
      <span class="brand-lockup__mark"></span>
      <h2 class="wordmark">Kelvaro.ch</h2>
    </div>
    <div class="services">
      <p>Vehicle labeling | Shop window labeling</p>
      <p>Stickers and much more ...</p>
    </div>
  </section>
</main>
</body>
</html>
```